Need a website to promote and sell my book

Using images from the book, I need a website designed that helps promote the book and eventually sell it.
*Need a landing page
*About the author page
*Storefront page to purchase
*Coming soon page
*"Featured in" page that can link to news articles etc.
The images posted here are examples, the winner of the contest will get the images from the finished book. I will provide the exact text to the winner of the contest.

I can also provide images of kids reading the book. For now, I'll just use one, the winner can have them all to choose from.
Updates

Extending deadline to allow for a few more designers to submit and to allow time for me to review and hold a poll

Target Market(s)

Parents, aunts, uncles, grandparents, friends who have kids; teachers, daycare teachers, babysitters etc.

Industry/Entity Type

Custom Publishing

Coding

Coded - Design and coding required

Number of Pages Required

5+ page

Font styles to use
Sans Serif

Colors

Designer to choose colors to be used in the design.

Requirements
Must have
• It must have a fun feel like the book.
Nice to have
• Would be great to have a section that automatically pulls tweets about the book into it.

```html
<!DOCTYPE html>
<html lang="en">
<head>
<meta charset="utf-8">
<title>Marisol Keane – About the Author</title>
<link href="https://fonts.googleapis.com/css2?family=Delius&family=Kalam:wght@400;700&display=swap" rel="stylesheet">
<style>
:root{
  --sky:#79d0e8;
  --sky-deep:#4fa9c9;
  --sun-top:#fbbf78;
  --sun-bottom:#eea548;
  --sun-edge:#e98a10;
  --plum-top:#750846;
  --plum-bottom:#4d0457;
  --coral:#f0676e;
  --red:#e8454d;
  --white:#ffffff;
  --ink-blue:#1f5c80;
  --star:#ffc400;
}
*{margin:0;padding:0;box-sizing:border-box}
html,body{width:1200px;height:2213px;overflow:hidden}
body{position:relative;font-family:"Delius",cursive;color:var(--white);background:var(--sky)}
.abs{position:absolute}

/* header */
.hero{left:0;top:0;width:1200px;height:418px;background:var(--sky)}
.doodle{position:absolute;border-radius:50%;background:rgba(47,140,180,.35)}
.brand{left:198px;top:60px;width:300px;font-family:"Kalam",cursive;font-weight:700;font-size:50px;line-height:54px;color:var(--white);text-align:center}
.nav{left:0;top:0;width:1200px;height:68px}
.nav a{position:absolute;top:33px;font-size:13px;color:var(--white);text-decoration:none}
.nav .purchase{left:976px;top:0;width:101px;height:67px;background:var(--white);border-radius:0 0 10px 10px;color:var(--sky-deep);text-align:center;padding-top:33px}
.portrait{left:123px;top:248px;width:275px;height:275px;border-radius:50%;border:5px solid var(--sun-edge);background:radial-gradient(circle at 50% 70%,#2a2a2a 0,#4b4040 30%,#b88a62 55%,#d8b795 100%)}
.kicker{left:497px;top:298px;font-family:"Kalam",cursive;font-size:20px;color:var(--red)}
.author-name{left:494px;top:318px;font-family:"Kalam",cursive;font-weight:700;font-size:54px;color:var(--white)}
.social-top{left:1000px;top:354px}
.social-top span{display:inline-block;width:14px;height:14px;border-radius:50%;background:var(--white);margin-right:15px}

/* about section */
.about{left:0;top:418px;width:1200px;height:660px;background:linear-gradient(var(--sun-top),var(--sun-bottom))}
.facts{font-size:13px;font-weight:700;color:var(--white)}
.facts span::before{content:"•";margin-right:6px}
.side-menu{left:136px;top:549px;width:253px}
.side-menu li{list-style:none;height:41.5px;padding-left:31px;line-height:42px;font-size:13px;font-weight:700;letter-spacing:.2px}
.side-menu li.active{background:rgba(236,160,60,.45);border-left:4px solid var(--sun-edge);padding-left:27px}
.bio{left:494px;top:533px;width:582px;font-size:12.6px;line-height:30.4px;color:var(--white)}

/* books */
.books{left:0;top:1000px;width:1200px;height:640px;background:linear-gradient(var(--plum-top),var(--plum-bottom))}
.section-title{left:169px;top:1112px;font-family:"Kalam",cursive;font-weight:700;font-size:34px}
.title-rule{left:170px;top:1172px;width:41px;height:2px;background:var(--white)}
.book{position:absolute;top:1235px;width:192px;text-align:center}
.cover{width:192px;height:192px;background:linear-gradient(#79d0e8 0,#79d0e8 60%,#f5b76a 100%)}
.book p{margin-top:14px;font-size:13px;line-height:16px}
.stars{margin-top:6px}

/* contact */
.contact{left:0;top:1560px;width:1200px;height:360px;background:var(--sky)}
.col-title{font-family:"Kalam",cursive;font-weight:700;font-size:15px;color:var(--ink-blue)}
.contact-line{font-size:13px;color:var(--ink-blue);line-height:16px}
.inquiry{left:673px;top:1733px;width:310px;font-size:12px;line-height:21px;color:#3d7ea1}

/* footer */
.footer{left:0;top:1911px;width:1200px;height:302px;background:var(--coral)}
.child-art{left:0;top:1868px;width:176px;height:280px;border-radius:80px 80px 60px 60px;background:linear-gradient(#c9875b,#8f8f9c)}
.subscribe-title{left:271px;top:1972px;font-family:"Kalam",cursive;font-weight:700;font-size:15px}
.subscribe{left:240px;top:2009px;width:351px;height:40px;border:2px solid var(--white);border-radius:20px}
.subscribe .field{position:absolute;left:28px;top:10px;font-size:13px;color:#fde0e1}
.subscribe .btn{position:absolute;right:3px;top:3px;width:110px;height:30px;border-radius:15px;background:var(--white);color:var(--coral);font-size:11px;text-align:center;line-height:30px}
.social-label{left:271px;top:2074px;font-family:"Kalam",cursive;font-weight:700;font-size:14px}
.social-foot{left:457px;top:2078px}
.social-foot span{display:inline-block;width:18px;height:18px;border-radius:50%;background:#f8b3b6;margin-right:19px}
.foot-links{left:703px;top:1972px}
.foot-links li{list-style:none;font-size:14px;line-height:30.5px}
.foot-brand{left:880px;top:1976px;width:200px;font-family:"Kalam",cursive;font-weight:700;font-size:36px;line-height:38px;text-align:center}
.copyright{left:0;top:2181px;width:1200px;text-align:center;font-size:11px;color:#fde0e1}
</style>
</head>
<body>

<section class="abs hero">
  <div class="doodle" style="left:45px;top:28px;width:92px;height:92px" role="img" aria-label="Football doodle"></div>
  <div class="doodle" style="left:575px;top:90px;width:120px;height:180px;border-radius:30px" role="img" aria-label="Microscope illustration"></div>
  <div class="doodle" style="left:755px;top:90px;width:110px;height:120px" role="img" aria-label="Test tube rack doodle"></div>
  <div class="doodle" style="left:905px;top:205px;width:120px;height:130px;border-radius:40px" role="img" aria-label="Flask illustration"></div>
  <div class="doodle" style="left:1035px;top:85px;width:80px;height:85px" role="img" aria-label="Atom doodle"></div>
  <div class="doodle" style="left:1110px;top:235px;width:90px;height:120px;border-radius:45px" role="img" aria-label="Molecule illustration"></div>
  <div class="doodle" style="left:80px;top:178px;width:80px;height:80px;border-radius:20px" role="img" aria-label="Syringe doodle"></div>
  <div class="doodle" style="left:370px;top:255px;width:92px;height:90px;border-radius:20px" role="img" aria-label="Lab stand doodle"></div>

  <div class="abs brand">Little Lab Adventures</div>

  <nav class="abs nav">
    <a style="left:544px">About Book</a>
    <a style="left:656px">About Marisol</a>
    <a style="left:791px">Featured On</a>
    <a style="left:904px">Contact</a>
    <a class="purchase">Purchase</a>
  </nav>

  <div class="abs kicker">A little bit about,</div>
  <h1 class="abs author-name">Marisol Keane</h1>
  <div class="abs social-top" role="img" aria-label="Social links"><span></span><span></span><span></span></div>
</section>

<section class="abs about">
  <div class="abs facts" style="left:497px;top:33px">
    <span>Author / Lecturer</span>
  </div>
  <div class="abs facts" style="left:718px;top:33px"><span>Volunteer at Tiny Towers</span></div>
  <div class="abs facts" style="left:497px;top:64px"><span>PhD in Sociology</span></div>
  <div class="abs facts" style="left:718px;top:64px"><span>Live in Brookdale, CA, USA</span></div>
</section>

<div class="abs portrait" role="img" aria-label="Portrait photo of the author outdoors"></div>

<ul class="abs side-menu">
  <li class="active">About Marisol</li>
  <li>Press</li>
  <li>Appearances</li>
  <li>Marisol’s Books</li>
  <li>Awards and Nominations</li>
</ul>

<p class="abs bio">Lorem ipsum dolor sit amet, consectetur adipiscing elit. Cras non enim congue, luctus nibh eget, egestas risus. Nunc quis convallis mi. Suspendisse sit amet dolor non lectus feugiat sollicitudin. Proin pretium mauris vel felis sollicitudin pretium. Vestibulum ornare congue est, in ullamcorper nisi fringilla vitae. Fusce a urna id ante pretium bibendum. Quisque quis mi diam. Fusce vitae diam et est consectetur pretium. Maecenas iaculis at risus vel malesuada. Integer mollis erat in erat pretium, nec laoreet tortor malesuada. Maecenas ligula quam, condimentum maximus mi hendrerit, tincidunt suscipit tellus. Nullam consectetur, purus egestas facilisis euismod, ex dolor dignissim ex, non molestie sapien ex ut magna. Lorem ipsum dolor sit amet, consectetur adipiscing elit. Sed ligula magna, commodo ac tellus in, fringilla vestibulum nunc. Proin aliquet, libero sit amet tempus interdum, lacus neque dapibus elit, ut blandit dui sem in velit. Donec ipsum erat, viverra ac vestibulum at, vulputate eu nunc.</p>

<section class="abs books">
  <svg class="abs" style="left:0;top:0" width="1200" height="70" viewBox="0 0 1200 70" aria-hidden="true">
    <path d="M0 0 H1200 V63 C1050 70 850 55 600 40 C400 10 200 0 0 20 Z" fill="var(--sun-edge)"/>
    <path d="M0 0 H1200 V56 C1050 64 850 50 600 34 C400 4 200 -6 0 14 Z" fill="var(--sun-bottom)"/>
  </svg>
</section>

<h2 class="abs section-title">Marisol’s latest books</h2>
<div class="abs title-rule"></div>

<div class="book" style="left:120px">
  <div class="cover" role="img" aria-label="Book cover: children reading among science doodles"></div>
  <p>Little Lab<br>Adventures</p>
  <svg class="stars" width="88" height="14" viewBox="0 0 88 14" aria-label="Five stars"><g fill="var(--star)"><polygon id="st" points="7,0 8.8,4.8 14,5 10,8.3 11.3,13.5 7,10.6 2.7,13.5 4,8.3 0,5 5.2,4.8"/><use href="#st" x="18.5"/><use href="#st" x="37"/><use href="#st" x="55.5"/><use href="#st" x="74"/></g></svg>
</div>
<div class="book" style="left:376px">
  <div class="cover" role="img" aria-label="Book cover: children reading among science doodles"></div>
  <p>Sample book 02</p>
  <svg class="stars" width="88" height="14" viewBox="0 0 88 14" aria-label="Five stars"><g fill="var(--star)"><use href="#st"/><use href="#st" x="18.5"/><use href="#st" x="37"/><use href="#st" x="55.5"/><use href="#st" x="74"/></g></svg>
</div>
<div class="book" style="left:633px">
  <div class="cover" role="img" aria-label="Book cover: children reading among science doodles"></div>
  <p>Sample book 03</p>
  <svg class="stars" width="88" height="14" viewBox="0 0 88 14" aria-label="Five stars"><g fill="var(--star)"><use href="#st"/><use href="#st" x="18.5"/><use href="#st" x="37"/><use href="#st" x="55.5"/><use href="#st" x="74"/></g></svg>
</div>
<div class="book" style="left:884px">
  <div class="cover" role="img" aria-label="Book cover: children reading among science doodles"></div>
  <p>Sample book 04</p>
  <svg class="stars" width="88" height="14" viewBox="0 0 88 14" aria-label="Five stars"><g fill="var(--star)"><use href="#st"/><use href="#st" x="18.5"/><use href="#st" x="37"/><use href="#st" x="55.5"/><use href="#st" x="74"/></g></svg>
</div>

<section class="abs contact">
  <svg class="abs" style="left:0;top:-24px" width="1200" height="120" viewBox="0 0 1200 120" aria-hidden="true">
    <path d="M0 75 C40 45 110 40 160 80 C250 30 400 40 488 110 C560 60 640 60 690 108 C740 70 790 70 820 92 C900 60 920 40 960 40 C1010 0 1150 -10 1200 20 V120 H0 Z" fill="var(--sky)"/>
  </svg>
</section>

<div class="abs col-title" style="left:271px;top:1687px">Send all your thoughts;</div>
<svg class="abs" style="left:271px;top:1733px" width="14" height="14" viewBox="0 0 14 14" aria-hidden="true"><path d="M3 0 L5 3.5 L3.6 5 C4.5 7.5 6.5 9.5 9 10.4 L10.5 9 L14 11 L12.5 13.6 C6 13 1 8 0.4 1.5 Z" fill="var(--ink-blue)"/></svg>
<div class="abs contact-line" style="left:299px;top:1733px">555-014-2280</div>
<svg class="abs" style="left:271px;top:1767px" width="14" height="11" viewBox="0 0 14 11" aria-hidden="true"><rect width="14" height="11" rx="1" fill="var(--ink-blue)"/><path d="M0.5 1 L7 6 L13.5 1" stroke="var(--sky)" fill="none"/></svg>
<div class="abs contact-line" style="left:299px;top:1764px">hello@keanelearning.com</div>
<svg class="abs" style="left:272px;top:1795px" width="12" height="16" viewBox="0 0 12 16" aria-hidden="true"><path d="M6 0 C2.7 0 0 2.6 0 6 C0 10 6 16 6 16 C6 16 12 10 12 6 C12 2.6 9.3 0 6 0 Z" fill="var(--ink-blue)"/><circle cx="6" cy="6" r="2.2" fill="var(--sky)"/></svg>
<div class="abs contact-line" style="left:299px;top:1796px">412 Maple Crest Rd, Fairhaven,<br>CA 90000,<br>USA.</div>

<div class="abs col-title" style="left:673px;top:1687px">For Inquiries</div>
<p class="abs inquiry">Lorem ipsum dolor sit amet, consectetur adipiscing elit. Cras non enim congue, luctus nibh eget, egestas risus. Nunc quis convallis mi.</p>
<div class="abs contact-line" style="left:673px;top:1818px">contact@keanelearning.com</div>

<footer class="abs footer">
  <svg class="abs" style="left:0;top:-5px" width="1200" height="6" viewBox="0 0 1200 6" preserveAspectRatio="none" aria-hidden="true">
    <path d="M0 6 L0 3 Q5 0 10 3 T20 3 T30 3 T40 3 T50 3 T60 3 T70 3 T80 3 T90 3 T100 3 T110 3 T120 3 T130 3 T140 3 T150 3 T160 3 T170 3 T180 3 T190 3 T200 3 T210 3 T220 3 T230 3 T240 3 T250 3 T260 3 T270 3 T280 3 T290 3 T300 3 T310 3 T320 3 T330 3 T340 3 T350 3 T360 3 T370 3 T380 3 T390 3 T400 3 T410 3 T420 3 T430 3 T440 3 T450 3 T460 3 T470 3 T480 3 T490 3 T500 3 T510 3 T520 3 T530 3 T540 3 T550 3 T560 3 T570 3 T580 3 T590 3 T600 3 T610 3 T620 3 T630 3 T640 3 T650 3 T660 3 T670 3 T680 3 T690 3 T700 3 T710 3 T720 3 T730 3 T740 3 T750 3 T760 3 T770 3 T780 3 T790 3 T800 3 T810 3 T820 3 T830 3 T840 3 T850 3 T860 3 T870 3 T880 3 T890 3 T900 3 T910 3 T920 3 T930 3 T940 3 T950 3 T960 3 T970 3 T980 3 T990 3 T1000 3 T1010 3 T1020 3 T1030 3 T1040 3 T1050 3 T1060 3 T1070 3 T1080 3 T1090 3 T1100 3 T1110 3 T1120 3 T1130 3 T1140 3 T1150 3 T1160 3 T1170 3 T1180 3 T1190 3 T1200 3 L1200 6 Z" fill="var(--coral)"/>
  </svg>
</footer>

<div class="abs child-art" role="img" aria-label="Illustration of a child hugging a toy elephant"></div>

<div class="abs subscribe-title">Subscribe us for latest news.!</div>
<div class="abs subscribe">
  <span class="field">your email</span>
  <span class="btn">Subscribe</span>
</div>
<div class="abs social-label">We’re on social :</div>
<div class="abs social-foot" role="img" aria-label="Social links"><span></span><span></span><span></span><span></span></div>

<ul class="abs foot-links">
  <li>About author</li>
  <li>Featured on</li>
  <li>Purchase</li>
  <li>Contact</li>
</ul>

<div class="abs foot-brand">Little Lab Adventures</div>

<div class="abs copyright">©2020 www.littlelabbook.com All rights reserved.</div>

</body>
</html>
```